Structural Engineering Business Card

Brookvane Drafting does residential house plans for clients in Central Florida. Would like simple but elegant business card that is appropriate for a house plan engineering company. Prefer black business card with black/white them but open to other shades of blue. I uploaded a sample card that I came across that looked good but please come up with your own creative designs.

Contact Information for Business Card

Name, Title, Phone, Email, Address, website

```html
<!DOCTYPE html>
<html lang="en">
<head>
<meta charset="utf-8">
<title>Brookvane Drafting — Business Card</title>
<link href="https://fonts.googleapis.com/css2?family=Arimo:wght@400;700&display=swap" rel="stylesheet">
<style>
  :root {
    --stage: #e6e6e6;
    --card-light: #ffffff;
    --card-dark: #3b3b3d;
    --ink: #2b2b2b;
    --ink-soft: #7a7a7a;
    --rule: #9a9a9a;
    --stripe: #2b2b2b;
    --paper-white: #ffffff;
  }
  * { box-sizing: border-box; margin: 0; padding: 0; }
  html, body {
    width: 1200px; height: 802px; overflow: hidden;
    background: var(--stage);
    font-family: "Arimo", Arial, sans-serif;
  }
  .stage {
    width: 1200px; height: 802px;
    display: flex; align-items: center; justify-content: center; gap: 60px;
  }
  .card {
    position: relative;
    width: 520px; height: 298px;
    box-shadow: 0 6px 18px rgba(0,0,0,0.12);
    overflow: hidden;
  }
  /* Front */
  .card--front { background: var(--card-light); color: var(--ink); }
  .card--front .brand {
    position: absolute; top: 40px; left: 0; right: 0;
    display: flex; align-items: center; justify-content: center; gap: 10px;
  }
  .brand__square { width: 18px; height: 18px; background: var(--ink); }
  .brand__name {
    font-weight: 700; font-size: 30px; letter-spacing: 0.5px; text-transform: uppercase;
  }
  .card--front .divider {
    position: absolute; left: 40px; right: 40px; top: 120px;
    height: 1px; background: var(--rule);
  }
  .holder { position: absolute; left: 40px; top: 150px; }
  .holder__name { font-weight: 700; font-size: 17px; letter-spacing: 0.5px; }
  .holder__title { font-size: 14px; color: var(--ink-soft); margin-top: 2px; }
  .holder__rule { width: 160px; height: 1px; background: var(--rule); margin: 10px 0 8px; }
  .contacts { list-style: none; font-size: 13.5px; color: var(--ink-soft); }
  .contacts li { display: flex; align-items: center; gap: 8px; line-height: 21px; }
  .contacts svg { width: 11px; height: 11px; fill: var(--ink); flex: none; }
  .address {
    position: absolute; right: 40px; top: 150px;
    text-align: right; font-size: 14px; color: var(--ink-soft); line-height: 20px;
  }
  .edge-stripes {
    position: absolute; left: 0; right: 0; bottom: 0; height: 14px;
    border-top: 4px solid var(--stripe);
    border-bottom: 6px solid var(--stripe);
  }
  /* Back */
  .card--back {
    background: var(--card-dark); color: var(--paper-white);
    display: flex; align-items: center; justify-content: center;
  }
  .card--back .brand { display: flex; align-items: center; gap: 12px; }
  .card--back .brand__square { background: var(--paper-white); width: 22px; height: 22px; }
  .card--back .brand__name { font-size: 36px; }
</style>
</head>
<body>
<main class="stage">
  <section class="card card--front">
    <div class="brand">
      <span class="brand__square"></span>
      <span class="brand__name">Brookvane Drafting</span>
    </div>
    <div class="divider"></div>
    <div class="holder">
      <p class="holder__name">DANIEL REYES</p>
      <p class="holder__title">Manager</p>
      <div class="holder__rule"></div>
      <ul class="contacts">
        <li><svg viewBox="0 0 12 12"><path d="M2.5 1l2 2.3-1 1.2a6 6 0 0 0 4 4l1.2-1 2.3 2-1.3 1.5C5 11 1 7 1 2.3z"/></svg>555-014-2100</li>
        <li><svg viewBox="0 0 12 12"><path d="M0 2h12v8H0z M1 3l5 3.5L11 3"/></svg>hello@brookvanedrafting.com</li>
        <li><svg viewBox="0 0 12 12"><circle cx="6" cy="6" r="6"/></svg>www.brookvanedrafting.com</li>
      </ul>
    </div>
    <p class="address">Your Address, City<br>State, Zip 0000</p>
    <div class="edge-stripes"></div>
  </section>

  <section class="card card--back">
    <div class="brand">
      <span class="brand__square"></span>
      <span class="brand__name">Brookvane Drafting</span>
    </div>
  </section>
</main>
</body>
</html>
```